Etiketten-Design für nachhaltige Rasur- & Pflegeprodukte
> Wir suchen Verpackung und Etiketten für eine Marke für nachhaltige Rasur- & Pflegeprodukte.
Habedere liebe Designer,
„Habedere“ sagt man bei uns in Bayern, es bedeutet Hallo oder auf Wiedersehen, je nach Gelegenheit. In diesem Fall: Hallo.
Vielleicht kennst du uns schon, wir sind greenpines, wir betreiben einen kleinen Shop für Bartpflege & Rasur unter greenpines-shop.de und wir versuchen uns nun an einem neuen Thema: nachhaltige Rasur- & Pflegeprodukte für Frauen.
Das machen wir unter dem Namen „Sanft“.
Weil die Frage schon oft aufkam: Jawohl, wir haben uns dafür die Beine und die Achseln mit einem Rasierhobel rasiert.
> Zielgruppe.
Wir arbeiten an einer neuen Pflegelinie für Frauen, die sich vorwiegend mit der Rasur und den dazugehörigen Pflegeprodukten beschäftigt. Die Zielgruppe sind vor allem online-affine Frauen aus Deutschland, Österreich und der Schweiz, aber sicher auch europaweit im Alter von 21-45.
> Aufgabenstellung.
Wir sind auf der Suche nach einem Konzept für unsere Produktverpackungen bzw. Etiketten. Bei den Pflegeprodukten verzichten wir bewusst auf eine Umverpackung.
Konkret geplant sind ein Rasierhobel, dafür haben wir eine schöne Umverpackung. Außerdem starten wir mit Rasieröl, Rasierseife und einem After Shave Balsam. Es werden später noch andere Artikel dazukommen, eine Deocreme zum Beispiel.
Rasieröl, Rasiercreme und After Shave Balsam duften nach Orangen, es werden zwei oder drei weitere Duftrichtungen folgen, die eine wird beispielsweise nach Beeren duften, die andere nach Pfirsich und Mango – bitte beachte das bei der Erstellung des Konzeptes, die Unterschiede sollten später auf den ersten Blick erkennbar sein.
Zurück zum Thema Orange: Wir würden den Duft als leicht herben Zitrusduft bezeichnen.
> Die Maße.
• Umverpackung Rasierhobel, weißer Karton (165x90x40mm)
• Rasieröl 30ml (Etikett: 100x46mm)
• Rasiercreme 60ml (Etikett: 156x32mm)
• After Shave Balsam 60ml (Etikett: 156x32mm)
> Zwingend erforderliche Angaben.
Da es sich um Kosmetikprodukte handelt, sind einige Angaben auf dem Label zwingend erforderlich, beispielhaft sollen die folgenden Infos als Platzhalter dienen.
• Hergestellt für Friedrich Lautner e.K. von greenpines, Lindenhofweg 7, 83109 Kolbermoor
• Ingredients: Aqua, Stearic Acid, Cocos Nucifera oil, Glycerin, Potassium Hydroxide, Litsea Cubeba oil, (and) Citrus Sinensis Peel oil, Orbignya Oleifera oil, Sodium Hydroxide, Macadamia ternifolia oil, Talc, Kaolin, Citric Acid, Simmondsia chinensis oil, Maris sal, C.I. 77892 (and) Rad Clay, Citral, Limonene, Linalool, Geraniol
• Platz für einen Barcode
• Rasieröl sind 30ml / 1.01 FL.OZ. ODER Creme & Balsam jeweils 60ml / 2.03 FL. OZ.
Wir haben ein Bild der aktuellen Gefäße beigefügt, es kann aber durchaus sein, dass wir uns noch umen..

```html
<!DOCTYPE html>
<html lang="de">
<head>
<meta charset="utf-8">
<title>Sanft – Rasieröl Etiketten</title>
<link rel="stylesheet" href="https://fonts.googleapis.com/css2?family=Comfortaa:wght@300;400&family=Cormorant+Garamond:wght@700&family=Noto+Sans:wght@400;600&display=swap">
<style>
  :root {
    --page: #f1eeea;
    --label: #26282a;
    --label-edge: #3a3c3e;
    --text-light: #d9d9d9;
    --text-muted: #bdbdbd;
    --ink-dark: #1c1c1c;
    --beeren: #c9a2cf;
    --beeren-accent: #6c3a74;
    --mango: #f2a91e;
    --mango-accent: #e0850f;
    --pfirsich: #f0b55c;
    --pfirsich-accent: #d8603a;
    --orange: #f7931c;
    --orange-accent: #e2620f;
  }
  * { box-sizing: border-box; margin: 0; padding: 0; }
  html, body { width: 667px; height: 1200px; overflow: hidden; background: var(--page); }
  .sheet {
    width: 667px; height: 1200px;
    display: grid;
    grid-template-rows: repeat(4, 1fr);
    padding: 24px 0;
    row-gap: 16px;
  }
  .scent-row { display: flex; justify-content: center; align-items: center; gap: 56px; }
  .scent-row.beeren { --tone: var(--beeren); --accent: var(--beeren-accent); }
  .scent-row.mango { --tone: var(--mango); --accent: var(--mango-accent); }
  .scent-row.pfirsich { --tone: var(--pfirsich); --accent: var(--pfirsich-accent); }
  .scent-row.orange { --tone: var(--orange); --accent: var(--orange-accent); }

  .label {
    width: 200px; height: 260px;
    background: var(--label);
    border: 1px solid var(--label-edge);
    border-radius: 4px;
    box-shadow: 0 2px 6px rgba(0,0,0,.15);
    position: relative;
    overflow: hidden;
  }

  /* Front label */
  .label-front { display: flex; flex-direction: column; align-items: center; }
  .brand-name {
    margin-top: 52px;
    font-family: "Comfortaa", sans-serif; font-weight: 300;
    font-size: 34px; line-height: 1; color: var(--text-light);
  }
  .product-name {
    margin-top: 38px;
    font-family: "Cormorant Garamond", serif; font-weight: 700;
    font-size: 22px; line-height: 1.1; color: var(--text-muted); letter-spacing: .5px;
  }
  .scent-band {
    position: absolute; left: 0; right: 0; bottom: 12px;
    height: 66px; background: var(--tone);
    border-top: 6px solid var(--accent);
    display: flex; flex-direction: column; align-items: center; justify-content: center;
  }
  .scent-name {
    font-family: "Comfortaa", sans-serif; font-weight: 400;
    font-size: 24px; letter-spacing: 2px; color: var(--ink-dark);
  }
  .volume { margin-top: 4px; font-family: "Noto Sans", sans-serif; font-size: 7px; color: var(--ink-dark); }

  /* Back label */
  .label-back { padding: 14px 14px 12px; color: var(--text-light); font-family: "Noto Sans", sans-serif; }
  .back-head { display: flex; align-items: flex-start; justify-content: space-between; gap: 10px; }
  .brand-name-small {
    font-family: "Comfortaa", sans-serif; font-weight: 300;
    font-size: 12px; line-height: 20px; color: var(--text-light);
  }
  .back-title { text-align: right; }
  .back-title .product-name { margin: 0; font-size: 16px; display: block; }
  .back-title .scent-tag { font-family: "Comfortaa", sans-serif; font-size: 9px; color: var(--tone); }
  .maker { margin-top: 10px; font-size: 7px; line-height: 1.35; text-align: center; }
  .ingredients-head { margin-top: 10px; font-size: 7px; font-weight: 600; color: var(--tone); }
  .ingredients { margin-top: 4px; font-size: 6.6px; line-height: 1.45; text-align: justify; }
  .back-volume { position: absolute; left: 14px; bottom: 12px; font-size: 9px; line-height: 1.2; }
</style>
</head>
<body>
<main class="sheet">

  <section class="scent-row beeren">
    <article class="label label-front">
      <span class="brand-name">Sanft</span>
      <h2 class="product-name">Rasieröl sind</h2>
      <div class="scent-band"><span class="scent-name">Beeren</span><span class="volume">30 ml/1.01 FL.OZ.</span></div>
    </article>
    <article class="label label-back">
      <header class="back-head">
        <span class="brand-name-small">Sanft</span>
        <div class="back-title"><span class="product-name">Rasieröl sind</span><span class="scent-tag">Beeren</span></div>
      </header>
      <p class="maker">Hergestellt für Friedrich Lautner e.K. von greenpines, Lindenhofweg 7, 83109 Kolbermoor.</p>
      <p class="ingredients-head">Ingredients:</p>
      <p class="ingredients">Aqua, Stearic Acid, Cocos Nucifera oil, Glycerin, Potassium Hydroxide, Litsea Cubeba oil, (and) Citrus Sinensis Peel oil, Orbignya Oleifera oil, Sodium Hydroxide, Macadamia ternifolia oil, Talc, Kaolin, Citric Acid, Simmondsia chinensis oil, Maris sal, C.I. 77892 (and) Rad Clay, Citral, Limonene, Linalool, Geraniol.</p>
      <p class="back-volume">30 ml/<br>1.01 FL.OZ.</p>
    </article>
  </section>

  <section class="scent-row mango">
    <article class="label label-front">
      <span class="brand-name">Sanft</span>
      <h2 class="product-name">Rasieröl sind</h2>
      <div class="scent-band"><span class="scent-name">Mango</span><span class="volume">30 ml/1.01 FL.OZ.</span></div>
    </article>
    <article class="label label-back">
      <header class="back-head">
        <span class="brand-name-small">Sanft</span>
        <div class="back-title"><span class="product-name">Rasieröl sind</span><span class="scent-tag">Mango</span></div>
      </header>
      <p class="maker">Hergestellt für Friedrich Lautner e.K. von greenpines, Lindenhofweg 7, 83109 Kolbermoor.</p>
      <p class="ingredients-head">Ingredients:</p>
      <p class="ingredients">Aqua, Stearic Acid, Cocos Nucifera oil, Glycerin, Potassium Hydroxide, Litsea Cubeba oil, (and) Citrus Sinensis Peel oil, Orbignya Oleifera oil, Sodium Hydroxide, Macadamia ternifolia oil, Talc, Kaolin, Citric Acid, Simmondsia chinensis oil, Maris sal, C.I. 77892 (and) Rad Clay, Citral, Limonene, Linalool, Geraniol.</p>
      <p class="back-volume">30 ml/<br>1.01 FL.OZ.</p>
    </article>
  </section>

  <section class="scent-row pfirsich">
    <article class="label label-front">
      <span class="brand-name">Sanft</span>
      <h2 class="product-name">Rasieröl sind</h2>
      <div class="scent-band"><span class="scent-name">Pfirsich</span><span class="volume">30 ml/1.01 FL.OZ.</span></div>
    </article>
    <article class="label label-back">
      <header class="back-head">
        <span class="brand-name-small">Sanft</span>
        <div class="back-title"><span class="product-name">Rasieröl sind</span><span class="scent-tag">Pfirsich</span></div>
      </header>
      <p class="maker">Hergestellt für Friedrich Lautner e.K. von greenpines, Lindenhofweg 7, 83109 Kolbermoor.</p>
      <p class="ingredients-head">Ingredients:</p>
      <p class="ingredients">Aqua, Stearic Acid, Cocos Nucifera oil, Glycerin, Potassium Hydroxide, Litsea Cubeba oil, (and) Citrus Sinensis Peel oil, Orbignya Oleifera oil, Sodium Hydroxide, Macadamia ternifolia oil, Talc, Kaolin, Citric Acid, Simmondsia chinensis oil, Maris sal, C.I. 77892 (and) Rad Clay, Citral, Limonene, Linalool, Geraniol.</p>
      <p class="back-volume">30 ml/<br>1.01 FL.OZ.</p>
    </article>
  </section>

  <section class="scent-row orange">
    <article class="label label-front">
      <span class="brand-name">Sanft</span>
      <h2 class="product-name">Rasieröl sind</h2>
      <div class="scent-band"><span class="scent-name">Orange</span><span class="volume">30 ml/1.01 FL.OZ.</span></div>
    </article>
    <article class="label label-back">
      <header class="back-head">
        <span class="brand-name-small">Sanft</span>
        <div class="back-title"><span class="product-name">Rasieröl sind</span><span class="scent-tag">Orange</span></div>
      </header>
      <p class="maker">Hergestellt für Friedrich Lautner e.K. von greenpines, Lindenhofweg 7, 83109 Kolbermoor.</p>
      <p class="ingredients-head">Ingredients:</p>
      <p class="ingredients">Aqua, Stearic Acid, Cocos Nucifera oil, Glycerin, Potassium Hydroxide, Litsea Cubeba oil, (and) Citrus Sinensis Peel oil, Orbignya Oleifera oil, Sodium Hydroxide, Macadamia ternifolia oil, Talc, Kaolin, Citric Acid, Simmondsia chinensis oil, Maris sal, C.I. 77892 (and) Rad Clay, Citral, Limonene, Linalool, Geraniol.</p>
      <p class="back-volume">30 ml/<br>1.01 FL.OZ.</p>
    </article>
  </section>

</main>
</body>
</html>
```